Kelvo bottle Label (Yoghurt drink)

Label for a 300 ml yoghurt drink bottle in 3 flavours.

General description:
• This is to design a sleeve shrink label for a Yoghurt Drink bottle in three flavours, Classic, Strawberry and Blueberry.
• Attached 3 photos: The one with KELVO brand in the current design we want to replace using the same bottle.
• Graphically, the design is to be similar to the examples provided for drumelo and fizzcrate.
• Use font and barcode size to be readable and legal.
• Minimize the use of the upper third of the bottle as it will be distorted when the label shrinks to the bottle.
• Professional and experienced designers only are welcome, please do not waste your time otherwise.

Bottle dimensions:
• Base across: 61 mm
• Height: 145 mm (approximate)

Graphical description:
• White colour with bands at the top and bottom similar to the one in “drumelo” example provided (not necessarily identical, feel free to be creative.
• The upper and lower bands to be: Green for “classic”, Pink or red for strawberry and purple for blueberry flavour.
• On the front: the brand name “Kelvo” and description “Yoghurt Drink” to be graphically attractive.
• On the front: two or more pieces of strawberry or blueberry for each flavour placed nicely with the option to include “yoghurt splash” or any suitable affects you deem suitable.
• For the Classic flavour, use the words (Classic, Lassi, Ayran) in the same location for the berries done in a graphically suitable manner.
• Colour temperature for the three flavours to be similar.

Information and objects on the label:
Front:
• The word “Kelvo” (brand name)
• “Yoghurt drink” (Product description)
• “300 ml” (size)
• Picture of Strawberries for strawberry flavour.
• Picture of Blueberries for blueberry flavour.
• The words (Classic, Lassi, Ayran) in the place used for the strawberries in the flavoured type, distributed to look graphically suitable for the overall design.

Back:
• Ingredient: Milk/milk solids, culture, salt, water, sugar, colour, flavour. (this is to be finalized later)
• Nutrition information table: (to be provided later).
• Barcode (to be provided later)
• Product of Australia
• Morel Tunsley Pty Ltd, 5/14 Ferrit St, Malaga, WA 6090
• info@kelvo-example.com.au 0491 000 372
• Keep under 5⁰ C
• Best before date printed on the bottle
• Shake well (to be located on the side at the top)
• Recycle icon.

Health benefits: (to be located suitably, possibly on the side with vertical orientation)
• Rich in probiotic bacteria and vitamins.
• Improves digestion and bowel motion.
• Supports weight control and fat loss.

Target Market(s)

General consumers

Industry/Entity Type

Grocery Store

Font styles to use
Sans Serif

Colors
abd037
b768aa
f04a50

Requirements
Must have
• The details in the project description
• The design must be simple and neat.
• Please use the shape of the current bottle "Kelvo" as in the attached photo.
Should not have
• Busy, cluttered, or empty and incomplete designs.

```html
<!DOCTYPE html>
<html lang="en">
<head>
<meta charset="utf-8">
<title>Kelvo Yoghurt Drink Labels</title>
<link href="https://fonts.googleapis.com/css2?family=Quicksand:wght@400;600;700&display=swap" rel="stylesheet">
<style>
  :root {
    --strawberry: #e0464e;
    --strawberry-chip: #e35d60;
    --blueberry: #a95ba0;
    --blueberry-chip: #a35be0;
    --classic: #8fb12a;
    --classic-chip: #8cbd4a;
    --ink: #3a3a3a;
    --bottle-fill: #ffffff;
    --bottle-edge: #dcdcdc;
    --bottle-shade: #ececec;
    --page-bg: #ffffff;
  }
  * { margin: 0; padding: 0; box-sizing: border-box; }
  html, body {
    width: 1200px; height: 985px; overflow: hidden;
    background: var(--page-bg);
    font-family: "Quicksand", sans-serif;
  }
  .canvas { position: relative; width: 1200px; height: 985px; }
  .bottles { position: absolute; left: 0; top: 0; }
  .bottle-body { fill: url(#bodyShade); stroke: var(--bottle-edge); stroke-width: 1.2; }
  .bottle-cap { fill: url(#capShade); stroke: var(--bottle-edge); stroke-width: 1.2; }
  .bottle-ring { fill: var(--bottle-fill); stroke: var(--bottle-edge); stroke-width: 1.2; }

  .label {
    position: absolute; top: 0; width: 220px; text-align: center;
  }
  .label--strawberry { left: 198px; }
  .label--blueberry  { left: 486px; }
  .label--classic    { left: 792px; }

  .brand {
    position: absolute; left: 0; width: 220px;
    font-size: 58px; font-weight: 700; letter-spacing: 0; line-height: 1;
  }
  .descriptor {
    position: absolute; left: 0; width: 220px;
    font-size: 25px; font-weight: 700; color: var(--ink); line-height: 1;
  }
  .flavour {
    position: absolute; left: 0; width: 220px;
    font-size: 23px; font-weight: 400; color: var(--ink); letter-spacing: 1px; line-height: 1;
  }
  .visual { position: absolute; border-radius: 50%; }
  .variant-name {
    position: absolute; left: 0; width: 220px;
    font-size: 26px; font-weight: 700; color: var(--classic); line-height: 1;
  }
  .volume {
    position: absolute; left: 0; width: 220px;
    font-size: 15px; color: var(--ink); line-height: 1;
  }
  .colour-chip { position: absolute; left: 83px; width: 53px; height: 51px; }

  .label--strawberry .brand { color: var(--strawberry); top: 438px; }
  .label--strawberry .descriptor { top: 488px; }
  .label--strawberry .flavour { top: 514px; }
  .label--strawberry .volume { top: 714px; }
  .label--strawberry .colour-chip { top: 731px; background: var(--strawberry-chip); }
  .visual--strawberry {
    left: 6px; top: 540px; width: 208px; height: 170px;
    background: radial-gradient(ellipse at 50% 55%, #e23a40 0%, #e5555a 40%, rgba(120,180,80,0.55) 70%, rgba(255,255,255,0) 100%);
  }

  .label--blueberry .brand { color: var(--blueberry); top: 433px; }
  .label--blueberry .descriptor { top: 483px; }
  .label--blueberry .flavour { top: 509px; }
  .label--blueberry .volume { top: 712px; }
  .label--blueberry .colour-chip { top: 731px; background: var(--blueberry-chip); }
  .visual--blueberry {
    left: 20px; top: 535px; width: 185px; height: 170px;
    background: radial-gradient(ellipse at 45% 58%, #3c4a85 0%, #55659f 42%, rgba(80,160,70,0.5) 70%, rgba(255,255,255,0) 100%);
  }

  .label--classic .brand { color: var(--classic); top: 438px; }
  .label--classic .descriptor { top: 488px; }
  .label--classic .flavour { top: 514px; }
  .label--classic .variant-name { top: 676px; }
  .label--classic .volume { top: 712px; }
  .label--classic .colour-chip { top: 731px; background: var(--classic-chip); }
  .visual--classic {
    left: 8px; top: 548px; width: 204px; height: 122px;
    background: radial-gradient(ellipse at 50% 62%, #d9d9d9 0%, #ececec 50%, rgba(255,255,255,0) 100%);
  }
</style>
</head>
<body>
<main class="canvas">
  <svg class="bottles" width="1200" height="985" viewBox="0 0 1200 985" aria-hidden="true">
    <defs>
      <linearGradient id="bodyShade" x1="0" x2="1" y1="0" y2="0">
        <stop offset="0" stop-color="#efefef"/>
        <stop offset="0.12" stop-color="#ffffff"/>
        <stop offset="0.88" stop-color="#ffffff"/>
        <stop offset="1" stop-color="#ececec"/>
      </linearGradient>
      <linearGradient id="capShade" x1="0" x2="1" y1="0" y2="0">
        <stop offset="0" stop-color="#eeeeee"/>
        <stop offset="0.5" stop-color="#ffffff"/>
        <stop offset="1" stop-color="#eeeeee"/>
      </linearGradient>
      <g id="bottle">
        <path class="bottle-body" d="M 30 100 C 26 130 18 170 12 210 C 4 265 0 305 0 345 L 0 585 Q 0 607 22 608 L 198 608 Q 220 607 220 585 L 220 345 C 220 305 216 265 208 210 C 202 170 194 130 190 100 Z"/>
        <rect class="bottle-ring" x="32" y="84" width="156" height="18" rx="3"/>
        <rect class="bottle-ring" x="24" y="70" width="172" height="15" rx="4"/>
        <rect class="bottle-cap" x="28" y="0" width="164" height="70" rx="9"/>
      </g>
    </defs>
    <use href="#bottle" x="198" y="173"/>
    <use href="#bottle" x="486" y="173"/>
    <use href="#bottle" x="792" y="173"/>
  </svg>

  <section class="label label--strawberry">
    <h1 class="brand">KELVO</h1>
    <p class="descriptor">yoghurt drink</p>
    <p class="flavour">strawberry</p>
    <div class="visual visual--strawberry" role="img" aria-label="Photo of fresh strawberries with green leaves"></div>
    <p class="volume">300ml</p>
    <div class="colour-chip"></div>
  </section>

  <section class="label label--blueberry">
    <h1 class="brand">KELVO</h1>
    <p class="descriptor">yoghurt drink</p>
    <p class="flavour">blueberry</p>
    <div class="visual visual--blueberry" role="img" aria-label="Photo of three blueberries with green leaves"></div>
    <p class="volume">300ml</p>
    <div class="colour-chip"></div>
  </section>

  <section class="label label--classic">
    <h1 class="brand">KELVO</h1>
    <p class="descriptor">yoghurt drink</p>
    <p class="flavour">classic</p>
    <div class="visual visual--classic" role="img" aria-label="Photo of a white yoghurt splash"></div>
    <p class="variant-name">Ayran/Lassi</p>
    <p class="volume">300ml</p>
    <div class="colour-chip"></div>
  </section>
</main>
</body>
</html>
```